Established coffee roaster needs a coffee bag and label design

We need a new coffee bag design! PLEASE SEE THE DOCUMENT UPLOADED FOR DETAILS; COFFEE PACKAGING PROJECT TASK!
Coffee bag template attached. We will also need a pre-printed sticker label for changing coffee information. 3 Sticker label designed for one core coffee bag design. THANK YOU!!!

Went on vacation/holiday

```html
<!DOCTYPE html>
<html lang="en">
<head>
<meta charset="utf-8">
<title>Quiet Harbor Coffee Roasters – Bag Dieline</title>
<link rel="stylesheet" href="https://fonts.googleapis.com/css2?family=Montserrat:wght@400;500&family=Poppins:wght@300;400&display=swap">
<style>
  :root {
    --stage: #d9d9d9;
    --navy: #283655;
    --navy-light: #34446a;
    --blush: #e3cfc8;
    --paper: #ffffff;
    --ink: #1f2430;
    --roast-green: #1e5a45;
    --heading: "Montserrat", sans-serif;
    --body: "Poppins", sans-serif;
  }
  * { box-sizing: border-box; margin: 0; padding: 0; }
  html, body { width: 1019px; height: 1200px; overflow: hidden; background: var(--stage); }
  .dieline { position: absolute; left: 44px; top: 263px; width: 931px; height: 673px; }
  .panel { position: absolute; background: var(--navy); overflow: hidden; color: var(--blush); }
  .panel--spine-left { left: 0; top: 0; width: 198px; height: 474px; border-radius: 8px 0 0 8px; }
  .panel--back { left: 198px; top: 0; width: 267px; height: 474px; border-radius: 8px 8px 0 0; }
  .panel--spine-right { left: 465px; top: 0; width: 198px; height: 474px; border-radius: 8px; }
  .panel--front { left: 663px; top: 0; width: 268px; height: 474px; border-radius: 8px; }
  .panel--base { left: 198px; top: 474px; width: 267px; height: 199px; border-radius: 0 0 8px 8px; }
  .panel + .panel { border-left: 1px solid #1e2a44; }

  .floral { position: absolute; left: 0; width: 100%; }
  .floral--top { top: 0; height: 150px; background: linear-gradient(180deg, var(--navy-light), rgba(40,54,85,0)); }
  .floral--bottom { bottom: 0; height: 200px; background: linear-gradient(0deg, var(--navy-light), rgba(40,54,85,0)); }

  .spine-mark { position: absolute; top: 218px; width: 38px; height: 38px; border-radius: 50%; background: var(--blush); }
  .panel--spine-left .spine-mark { left: 61px; }
  .panel--spine-right .spine-mark { left: 101px; }
  .spine-brand { position: absolute; top: 237px; white-space: nowrap; }
  .panel--spine-left .spine-brand { left: 128px; transform: translate(-50%, -50%) rotate(-90deg); }
  .panel--spine-right .spine-brand { left: 72px; transform: translate(-50%, -50%) rotate(90deg); }
  .spine-brand__name { font-family: var(--heading); font-weight: 400; font-size: 15px; line-height: 13px; text-transform: uppercase; }
  .spine-brand__tag { font-family: var(--heading); font-size: 6px; letter-spacing: 3.3px; margin-top: 3px; }

  .back-copy { position: absolute; left: 35px; top: 157px; color: var(--paper); }
  .back-copy__lead { width: 172px; font-family: var(--heading); font-weight: 500; font-size: 8.6px; line-height: 10.6px; letter-spacing: 1px; text-transform: uppercase; }
  .back-copy__rule { width: 112px; height: 1px; background: rgba(255,255,255,.6); margin: 10px 0 12px; }
  .back-copy__body { width: 162px; font-family: var(--body); font-weight: 300; font-size: 7.6px; line-height: 12.7px; }
  .back-copy__contact { font-family: var(--body); font-weight: 300; font-size: 6px; line-height: 10.5px; margin-top: 14px; text-transform: uppercase; }
  .recycle { position: absolute; left: 35px; top: 388px; color: var(--paper); font-family: var(--body); font-weight: 300; font-size: 5px; line-height: 8.5px; text-transform: uppercase; }
  .recycle svg { display: block; margin-bottom: 3px; }
  .date-box { position: absolute; left: 158px; top: 385px; width: 76px; height: 41px; background: var(--paper); }
  .established { position: absolute; left: 0; width: 100%; top: 438px; text-align: center; color: var(--paper); font-family: var(--body); font-weight: 300; font-size: 5.2px; text-transform: uppercase; }

  .front-brand { position: absolute; left: 0; width: 100%; top: 140px; text-align: center; }
  .front-brand__mark { width: 52px; height: 52px; border-radius: 50%; background: var(--blush); margin: 0 auto 16px; }
  .front-brand__name { font-family: var(--heading); font-weight: 400; font-size: 18.5px; line-height: 16px; color: var(--blush); text-transform: uppercase; }
  .front-brand__tag { font-family: var(--heading); font-size: 7px; letter-spacing: 3.4px; color: var(--blush); margin-top: 3px; }

  .label { position: absolute; left: 44px; top: 278px; width: 182px; height: 124px; background: var(--paper); outline: 3px dotted var(--paper); color: var(--ink); }
  .label__name { position: absolute; left: 11px; top: 12px; font-family: var(--heading); font-weight: 500; font-size: 13.5px; letter-spacing: 1px; }
  .label__notes { position: absolute; left: 12px; top: 29px; font-family: var(--body); font-size: 4.6px; }
  .label__process { position: absolute; left: 11px; top: 50px; width: 86px; font-family: var(--heading); font-size: 5px; line-height: 6.6px; letter-spacing: .6px; }
  .label__vrule { position: absolute; width: 1px; background: var(--ink); }
  .label__vrule--top { left: 100px; top: 10px; height: 64px; }
  .label__vrule--a { left: 56px; top: 82px; height: 33px; }
  .label__vrule--b { left: 133px; top: 82px; height: 33px; }
  .label__hrule { position: absolute; left: 10px; top: 78px; width: 162px; height: 1px; background: var(--ink); }
  .label__roast { position: absolute; left: 111px; top: 16px; width: 54px; height: 54px; border-radius: 50%; background: var(--roast-green); }
  .label__best { position: absolute; left: 10px; top: 87px; font-family: var(--heading); font-size: 5px; line-height: 6px; letter-spacing: .6px; }
  .label__origin { position: absolute; left: 56px; width: 77px; top: 87px; text-align: center; font-family: var(--heading); font-size: 10px; line-height: 9.5px; letter-spacing: .8px; }
  .net-weight { position: absolute; right: 41px; top: 410px; font-family: var(--heading); font-size: 7.2px; letter-spacing: .8px; color: var(--blush); }
</style>
</head>
<body>
<main class="dieline">
  <section class="panel panel--spine-left">
    <div class="floral floral--top" role="img" aria-label="Line-art lotus flowers hanging from the top"></div>
    <div class="floral floral--bottom" role="img" aria-label="Line-art lotus flowers rising from the bottom"></div>
    <span class="spine-mark"></span>
    <div class="spine-brand">
      <p class="spine-brand__name">Quiet Harbor<br>Coffee Roasters</p>
      <p class="spine-brand__tag">SINGLE ORIGIN COFFEE</p>
    </div>
  </section>

  <section class="panel panel--back">
    <div class="back-copy">
      <p class="back-copy__lead">Quiet Harbor single origin coffee offers a pure, hand-crafted experience from farm to cup.</p>
      <div class="back-copy__rule"></div>
      <p class="back-copy__body">VALUES: Our core values, compassion, gratitude, honesty, humility, kindness, forgiveness, and patience are ideals that we strive for. Embrace a value and move forward with your daily life in a positive way!</p>
      <p class="back-copy__contact">Website address:<br>www.quietharborroast.com<br>@quietharborroast</p>
    </div>
    <div class="recycle">
      <svg width="11" height="10" viewBox="0 0 22 20" fill="none" stroke="#fff" stroke-width="2"><path d="M8 3 L11 1 L14 6 M17 8 L20 14 L17 18 H12 M5 18 H3 L1 14 L5 8"/><path d="M9 16 L12 18 L9 20 M15 4 L14 6 L11 5 M3 10 L5 8 L7 10"/></svg>
      Help protect al living things,<br>and please recycle this bag<br>after use.
    </div>
    <div class="date-box"></div>
    <p class="established">Established 2007 | Riverton, Oregon</p>
  </section>

  <section class="panel panel--spine-right">
    <div class="floral floral--top" role="img" aria-label="Line-art lotus flowers hanging from the top"></div>
    <div class="floral floral--bottom" role="img" aria-label="Line-art lotus flowers rising from the bottom"></div>
    <div class="spine-brand">
      <p class="spine-brand__name">Quiet Harbor<br>Coffee Roasters</p>
      <p class="spine-brand__tag">SINGLE ORIGIN COFFEE</p>
    </div>
    <span class="spine-mark"></span>
  </section>

  <section class="panel panel--front">
    <div class="front-brand">
      <div class="front-brand__mark"></div>
      <p class="front-brand__name">Quiet Harbor<br>Coffee Roasters</p>
      <p class="front-brand__tag">SINGLE ORIGIN COFFEE</p>
    </div>
    <div class="label">
      <p class="label__name">PATIENCE</p>
      <p class="label__notes">NUTTY | TOFFEE | FULL BODY</p>
      <p class="label__process">TBD (WASHED/NATURAL /HONEY/SWISS WATER PROCESS/OTHER)</p>
      <span class="label__vrule label__vrule--top"></span>
      <span class="label__roast"></span>
      <span class="label__hrule"></span>
      <p class="label__best">BEST<br>BEFORE<br>DATE</p>
      <span class="label__vrule label__vrule--a"></span>
      <p class="label__origin">ETHIOPIA<br>REKO</p>
      <span class="label__vrule label__vrule--b"></span>
    </div>
    <p class="net-weight">NET WEIGHT: 12OZ</p>
  </section>

  <section class="panel panel--base"></section>
</main>
</body>
</html>
```